Irrigation Business needs their business cards modernised and revamped

I would like to keep my current logo, colours and revamp the format of the card.

I would like the card to be clean yet important.

Im not sure if you include texture but i would like the named logo to be indented into the card etc.

show me something alive and free something thats clinical to the point yet has a feel of achievement. i would like people to go nice card.

Target Market(s)

high end clients, corporate, sports field manger, the guys that make the decisions

Industry/Entity Type

Business

Contact Information for Business Card

nformation to be included

Dean Harlow (Director)
0487305526
dean@kolvat.biz
www.kestonfieldworks.com

instagram logo
google logo
facebook logo

Colors

Designer to choose colors to be used in the design.

Requirements
Nice to have
• indentations a really nice feel to the card good texture

```html
<!DOCTYPE html>
<html lang="en">
<head>
<meta charset="utf-8">
<title>Keston Fieldworks – Business Card</title>
<link href="https://fonts.googleapis.com/css2?family=PT+Sans:wght@400;700&display=swap" rel="stylesheet">
<style>
  :root {
    --page: #eceef1;
    --white: #ffffff;
    --brand-blue: #2a5ea8;
    --sky-blue: #2ea3da;
    --deep-blue: #2e6db5;
    --field-green: #2fa55a;
    --card-shadow: rgba(20, 40, 70, 0.18);
  }
  * { box-sizing: border-box; margin: 0; padding: 0; }
  html, body {
    width: 1200px; height: 900px; overflow: hidden;
    background: var(--page);
    font-family: "PT Sans", sans-serif;
  }
  .canvas { position: relative; width: 1200px; height: 900px; }

  .card {
    position: absolute;
    overflow: hidden;
    box-shadow: 0 10px 28px var(--card-shadow);
  }

  /* Front */
  .card-front {
    left: 78px; top: 34px; width: 588px; height: 364px;
    background: var(--white);
  }
  .front-bands { position: absolute; inset: 0; }
  .brand {
    position: absolute; left: 0; right: 0; top: 26px;
    display: flex; flex-direction: column; align-items: center; gap: 16px;
  }
  .brand-dot {
    width: 92px; height: 92px; border-radius: 50%;
    background: var(--sky-blue);
  }
  .brand-name {
    font-weight: 700; font-size: 31px; letter-spacing: 0.5px;
    color: var(--brand-blue);
  }
  .contact {
    position: absolute; left: 24px; top: 269px;
    list-style: none; color: var(--white); font-size: 16px;
  }
  .contact li { display: flex; align-items: center; gap: 5px; height: 22px; }
  .contact svg { width: 15px; height: 15px; flex: none; }
  .person {
    position: absolute; right: 32px; top: 254px; text-align: right; color: var(--white);
  }
  .person-name { font-weight: 700; font-size: 21px; line-height: 1.1; }
  .person-role { font-size: 15px; line-height: 1.2; }
  .social {
    position: absolute; right: 34px; top: 310px; display: flex; gap: 7px;
  }
  .social span {
    width: 24px; height: 24px; border-radius: 50%; background: var(--white);
  }

  /* Back */
  .card-back {
    left: 388px; top: 505px; width: 567px; height: 352px;
    background: radial-gradient(circle at 50% 55%, var(--sky-blue) 0%, #2b8fd0 45%, var(--deep-blue) 100%);
  }
  .back-ring {
    position: absolute; left: 28px; top: 22px; width: 510px; height: 510px;
    border-radius: 50%; border: 22px solid rgba(255, 255, 255, 0.05);
  }
  .back-brand {
    position: absolute; inset: 0;
    display: flex; flex-direction: column; align-items: center; justify-content: center; gap: 14px;
  }
  .back-dot {
    width: 150px; height: 150px; border-radius: 50%;
    border: 5px solid var(--white);
  }
  .back-name { font-weight: 700; font-size: 24px; letter-spacing: 1px; color: var(--white); }
</style>
</head>
<body>
<main class="canvas">

  <section class="card card-front" aria-label="Business card front">
    <svg class="front-bands" width="588" height="364" viewBox="0 0 588 364" aria-hidden="true">
      <defs>
        <linearGradient id="front-blue" x1="0" y1="0" x2="0" y2="1">
          <stop offset="0" stop-color="#2ea3da"/>
          <stop offset="1" stop-color="#2e6db5"/>
        </linearGradient>
      </defs>
      <polygon points="0,207 395,207 379,237 0,237" fill="var(--field-green)"/>
      <polygon points="0,241 392,241 413,200 588,200 588,364 0,364" fill="url(#front-blue)"/>
    </svg>

    <div class="brand">
      <span class="brand-dot"></span>
      <span class="brand-name">KESTON FIELDWORKS</span>
    </div>

    <ul class="contact">
      <li>
        <svg viewBox="0 0 16 16"><circle cx="8" cy="8" r="8" fill="#fff"/><path d="M5 6.5c0-1 1-1.6 3-1.6s3 .6 3 1.6l-1 .3-.4-1H6.4l-.4 1zM5.6 8h4.8l.6 3H5z" fill="#2e8bd0"/></svg>
        0487305526
      </li>
      <li>
        <svg viewBox="0 0 16 16"><circle cx="8" cy="8" r="8" fill="#fff"/><rect x="4" y="5.2" width="8" height="5.6" fill="#2e8bd0"/><path d="M4 5.4l4 3 4-3" stroke="#fff" stroke-width="0.9" fill="none"/></svg>
        dean@kolvat.biz
      </li>
      <li>
        <svg viewBox="0 0 16 16"><circle cx="8" cy="8" r="8" fill="#fff"/><circle cx="8" cy="8" r="4" fill="none" stroke="#2e8bd0" stroke-width="1.2"/><path d="M4 8h8M8 4v8" stroke="#2e8bd0" stroke-width="1"/></svg>
        www.kestonfieldworks.com
      </li>
    </ul>

    <div class="person">
      <p class="person-name">DEAN HARLOW</p>
      <p class="person-role">Director</p>
    </div>

    <div class="social" aria-label="Social media">
      <span></span><span></span><span></span>
    </div>
  </section>

  <section class="card card-back" aria-label="Business card back">
    <div class="back-ring"></div>
    <div class="back-brand">
      <span class="back-dot"></span>
      <span class="back-name">KESTON FIELDWORKS</span>
    </div>
  </section>

</main>
</body>
</html>
```